Business Card Design

I already have a company logo for my company. I have a logo for the manufacturer we represent. I want a professional business card design.

```html
<!DOCTYPE html>
<html lang="en">
<head>
<meta charset="utf-8">
<title>Northgate Signal Co. — Business Card</title>
<link rel="stylesheet" href="https://fonts.googleapis.com/css2?family=Open+Sans:wght@400;600;700&display=swap">
<style>
  :root {
    --bg: #3b3b3d;
    --card-front: #ffffff;
    --card-back: #e8e8ea;
    --red: #e3262d;
    --gold: #c9a227;
    --ink: #3a3a3a;
    --ink-soft: #5a5a5a;
  }
  * { box-sizing: border-box; margin: 0; padding: 0; }
  html, body {
    width: 1200px; height: 900px; overflow: hidden;
    background: var(--bg);
    font-family: "Open Sans", Arial, sans-serif;
  }
  .canvas { position: relative; width: 1200px; height: 900px; }

  .card {
    position: absolute;
    width: 560px; height: 320px;
    border-radius: 26px;
    box-shadow: 0 14px 30px rgba(0,0,0,.45);
  }
  .card--back { left: 580px; top: 70px; background: var(--card-back); }
  .card--front { left: 60px; top: 470px; background: var(--card-front); }

  .wordmark {
    display: flex; align-items: center; gap: 10px;
    color: var(--red); font-weight: 700; letter-spacing: .5px;
  }
  .wordmark__dot { width: 16px; height: 16px; border-radius: 50%; background: var(--red); }

  .card--back .wordmark {
    position: absolute; left: 0; right: 0; top: 50%;
    transform: translateY(-50%); justify-content: center; font-size: 30px;
  }

  .card--front .wordmark--top {
    position: absolute; right: 44px; top: 44px; font-size: 24px;
  }

  .identity { position: absolute; left: 44px; top: 150px; width: 240px; }
  .identity__name { color: var(--red); font-weight: 700; font-size: 22px; }
  .identity__title { color: var(--ink-soft); font-size: 12px; margin-top: 2px; }
  .identity .wordmark { font-size: 18px; margin-top: 30px; }
  .identity__rule { height: 3px; width: 210px; background: var(--gold); margin-top: 6px; }

  .divider {
    position: absolute; left: 300px; top: 150px;
    width: 1.5px; height: 110px; background: var(--gold);
  }

  .contacts {
    position: absolute; left: 320px; top: 158px;
    list-style: none; color: var(--ink); font-size: 13px;
  }
  .contacts li { display: flex; align-items: center; gap: 8px; margin-bottom: 10px; }
  .contacts svg { width: 12px; height: 12px; flex: none; }
</style>
</head>
<body>
<main class="canvas">

  <section class="card card--back" aria-label="Card back">
    <div class="wordmark"><span class="wordmark__dot"></span>Northgate Signal Co.</div>
  </section>

  <section class="card card--front" aria-label="Card front">
    <div class="wordmark wordmark--top"><span class="wordmark__dot"></span>Northgate Signal Co.</div>

    <div class="identity">
      <p class="identity__name">Dana Whitfield</p>
      <p class="identity__title">Managing Director</p>
      <div class="wordmark">Northgate Signal Co.</div>
      <div class="identity__rule"></div>
    </div>

    <div class="divider"></div>

    <ul class="contacts">
      <li>
        <svg viewBox="0 0 12 12"><rect width="12" height="12" rx="3" fill="#e3262d"/><path d="M4 3.2l1 1.6-.6.6c.4.9 1 1.5 1.9 1.9l.6-.6 1.6 1-.5 1.1C5.6 8.7 3.3 6.4 3 4z" fill="#fff"/></svg>
        555.204.7781
      </li>
      <li>
        <svg viewBox="0 0 12 12"><rect width="12" height="12" rx="3" fill="#e3262d"/><rect x="2.5" y="3.5" width="7" height="5" fill="none" stroke="#fff" stroke-width="1"/><path d="M2.5 3.7L6 6.4l3.5-2.7" fill="none" stroke="#fff" stroke-width="1"/></svg>
        hello@northgatesignal.com
      </li>
      <li>
        <svg viewBox="0 0 12 12"><circle cx="6" cy="6" r="6" fill="#e3262d"/><circle cx="6" cy="6" r="3.4" fill="none" stroke="#fff" stroke-width=".9"/><path d="M2.6 6h6.8M6 2.6c-1.6 2-1.6 4.8 0 6.8M6 2.6c1.6 2 1.6 4.8 0 6.8" fill="none" stroke="#fff" stroke-width=".8"/></svg>
        www.northgatesignal.com
      </li>
    </ul>
  </section>

</main>
</body>
</html>
```